Building company buisness cards

We are looking for a sharp modern new look for our business cards.
We are a New Zealand based company that specialises in house and land packages.
We have attached a photo of the current logo and would like to see if it can be improved somehow if needed.
We are open to any colours but we have chosen green at this stage.
Feel free to change the font and make the logo smarter looking.
Play with the colours and see what looks best.

We want a card that looks so good know one will want to throw it away!

Target Market(s)

Home buyers

Industry/Entity Type

Building

Contact Information for Business Card

Derek Tolvane
0217394062
dtolvane@quillmarkhomesteads.co.nz
quillmarkhomesteads.co.nz

Font styles to use
Serif
Sans Serif

Colors

Designer to choose colors to be used in the design.

Requirements
Must have
• Logo and company name on one side, details on the other side
Nice to have
• Color codes for the original green are HEX #4a8028, RGB(74,128,40), CMYK(42,0,69,50)
• Round corners, Raised and/or spot UV

```html
<!DOCTYPE html>
<html lang="en">
<head>
<meta charset="utf-8">
<title>Quillmark Homesteads – Business Card</title>
<link href="https://fonts.googleapis.com/css2?family=Lato:wght@400;700;900&display=swap" rel="stylesheet">
<style>
  :root {
    --brand-green: #4a8028;
    --card-white: #fbfbfa;
    --page-bg: #e9eae7;
    --rule-green: #b9cfa9;
    --text-white: #ffffff;
  }
  html, body {
    margin: 0;
    padding: 0;
    width: 1200px;
    height: 900px;
    overflow: hidden;
    background: var(--page-bg);
  }
  .canvas {
    position: relative;
    width: 1200px;
    height: 900px;
    display: flex;
    align-items: center;
    justify-content: center;
  }
  .business-card {
    position: relative;
    width: 960px;
    height: 595px;
    background: var(--card-white);
    overflow: hidden;
    box-shadow: 0 10px 30px rgba(0,0,0,0.12);
    font-family: "Lato", Arial, sans-serif;
  }
  .card-shapes {
    position: absolute;
    inset: 0;
    width: 100%;
    height: 100%;
  }
  .holder-name {
    position: absolute;
    left: 48px;
    top: 172px;
    margin: 0;
    color: var(--text-white);
    font-size: 31px;
    font-weight: 700;
    letter-spacing: 0.3px;
    text-transform: uppercase;
  }
  .contact-list {
    position: absolute;
    left: 46px;
    top: 438px;
    margin: 0;
    padding: 0;
    list-style: none;
    color: var(--text-white);
    font-size: 26px;
    font-weight: 400;
    line-height: 35px;
  }
  .contact-list li {
    display: flex;
    align-items: center;
    gap: 12px;
  }
  .contact-icon {
    width: 22px;
    height: 22px;
    flex: none;
    fill: var(--text-white);
  }
  .company-name {
    position: absolute;
    left: 500px;
    width: 400px;
    top: 150px;
    margin: 0;
    text-align: center;
    color: var(--brand-green);
    font-size: 48px;
    font-weight: 900;
    line-height: 54px;
    letter-spacing: -0.3px;
  }
  .company-rule {
    position: absolute;
    left: 653px;
    top: 272px;
    width: 94px;
    height: 2px;
    background: var(--rule-green);
  }
</style>
</head>
<body>
  <main class="canvas">
    <section class="business-card">
      <svg class="card-shapes" viewBox="0 0 960 595" aria-hidden="true">
        <polygon points="0,0 266,0 708,595 0,595" fill="var(--brand-green)"/>
        <line x1="283" y1="0" x2="725" y2="595" stroke="var(--brand-green)" stroke-width="4"/>
      </svg>

      <h1 class="holder-name">Derek Tolvane</h1>

      <ul class="contact-list">
        <li>
          <svg class="contact-icon" viewBox="0 0 24 24" aria-hidden="true">
            <path d="M3 8c0-2 3-3.5 9-3.5S21 6 21 8v1.5h-4.5V8h-9v1.5H3z"/>
            <path d="M6 11h12l2 8H4z M12 12.5a3 3 0 1 0 0 6 3 3 0 1 0 0-6z" fill-rule="evenodd"/>
          </svg>
          <span>0217394062</span>
        </li>
        <li>
          <svg class="contact-icon" viewBox="0 0 24 24" aria-hidden="true">
            <path d="M3 6h18v12H3z"/>
            <polyline points="3.5,7 12,13 20.5,7" fill="none" stroke="var(--brand-green)" stroke-width="1.6"/>
          </svg>
          <span>dtolvane@quillmarkhomesteads.co.nz</span>
        </li>
        <li>
          <svg class="contact-icon" viewBox="0 0 24 24" aria-hidden="true">
            <circle cx="12" cy="12" r="9.5"/>
            <path d="M7 8c2-1 3 1 5 0s1 3-1 4-1 3-3 3-2-3-2-4 0-2 1-3z M14 14c2 0 3 1 3 2s-2 3-3 2-1-4 0-4z" fill="var(--brand-green)"/>
          </svg>
          <span>www.quillmarkhomesteads.co.nz</span>
        </li>
      </ul>

      <p class="company-name">Quillmark<br>Homesteads</p>
      <div class="company-rule"></div>
    </section>
  </main>
</body>
</html>
```